Corvel Capital LLC

Need Professional Business cards for New Investment Fund

Target Market(s)

High Quality investors

Industry/Entity Type

Financial

Contact Information for Business Card

Phone Number +1 555 284 6190
Name Lukas Varenko
Title Fund Manager
email lv@FundCorvel.com
Website www.FundCorvel.com

Colors

Designer to choose colors to be used in the design.

Requirements
Must have
• Must have our Logo and all of the above. Must be made so lettering and loge can be raised

```html
<!DOCTYPE html>
<html lang="en">
<head>
<meta charset="utf-8">
<title>Aldervane Capital — Business Card</title>
<link href="https://fonts.googleapis.com/css2?family=Lato:wght@400;700&display=swap" rel="stylesheet">
<style>
  :root {
    --backdrop: #2c2c2c;
    --paper: #ffffff;
    --brand-green: #22e60a;
    --brand-slate: #414d42;
    --ink: #1f1f1f;
    --rule: #9a9a9a;
  }
  html, body {
    margin: 0;
    width: 1200px;
    height: 1200px;
    overflow: hidden;
    background: var(--backdrop);
    font-family: "Lato", Arial, sans-serif;
  }
  .canvas {
    position: relative;
    width: 1200px;
    height: 1200px;
  }
  .card {
    position: absolute;
    top: 310px;
    width: 364px;
    height: 594px;
    box-shadow: 3px 4px 8px rgba(0,0,0,0.55);
    overflow: hidden;
  }
  .card--front {
    left: 234px;
    background: var(--paper);
  }
  .card--back {
    left: 627px;
    width: 370px;
    background: var(--brand-slate);
  }

  /* front */
  .brand-mark {
    position: absolute;
    top: 226px;
    left: 0;
    width: 100%;
    display: flex;
    align-items: center;
    justify-content: center;
    gap: 10px;
  }
  .brand-mark__square {
    width: 18px;
    height: 18px;
    background: var(--brand-green);
  }
  .brand-mark__name {
    font-size: 26px;
    font-weight: 700;
    letter-spacing: 2px;
    color: var(--brand-slate);
  }
  .holder {
    position: absolute;
    top: 382px;
    width: 100%;
    text-align: center;
  }
  .holder__name {
    margin: 0;
    font-size: 22px;
    font-weight: 700;
    letter-spacing: 0.5px;
    color: var(--brand-slate);
  }
  .holder__first { color: var(--brand-green); }
  .holder__title {
    margin: 1px 0 0;
    font-size: 17px;
    color: #333;
  }
  .contact-icons {
    position: absolute;
    top: 444px;
    left: 87px;
  }
  .contact {
    position: absolute;
    top: 472px;
    width: 100%;
    margin: 0;
    padding: 0;
    list-style: none;
    text-align: center;
    font-size: 17px;
    line-height: 21.5px;
    letter-spacing: 0.3px;
    color: var(--ink);
  }

  /* back */
  .back-split {
    position: absolute;
    top: 0;
    left: 0;
    width: 141px;
    height: 100%;
    background: var(--brand-green);
  }
  .back-name {
    position: absolute;
    top: 50%;
    left: 141px;
    width: 229px;
    transform: translateY(-50%);
    text-align: center;
    font-size: 30px;
    font-weight: 700;
    letter-spacing: 2px;
    color: var(--paper);
  }
</style>
</head>
<body>
<main class="canvas">

  <section class="card card--front" aria-label="Business card front">
    <div class="brand-mark">
      <span class="brand-mark__square"></span>
      <span class="brand-mark__name">ALDERVANE</span>
    </div>

    <div class="holder">
      <h1 class="holder__name"><span class="holder__first">LUKAS</span> VARENKO</h1>
      <p class="holder__title">Fund Manager</p>
    </div>

    <svg class="contact-icons" width="190" height="26" viewBox="0 0 190 26" aria-hidden="true">
      <line x1="0" y1="12" x2="52" y2="12" stroke="var(--rule)" stroke-width="1"/>
      <line x1="138" y1="12" x2="190" y2="12" stroke="var(--rule)" stroke-width="1"/>
      <circle cx="67" cy="12" r="12" fill="var(--brand-slate)"/>
      <path d="M61 9 q6 -5 12 0 l-2 2 h-2 v-1 q-2 -1 -4 0 v1 h-2 z M62 12 h10 v5 h-10 z" fill="#fff"/>
      <circle cx="95" cy="12" r="12" fill="var(--brand-slate)"/>
      <rect x="88" y="7" width="14" height="10" fill="none" stroke="#fff" stroke-width="1.5"/>
      <polyline points="88,7 95,13 102,7" fill="none" stroke="#fff" stroke-width="1.5"/>
      <circle cx="123" cy="12" r="12" fill="var(--brand-slate)"/>
      <circle cx="123" cy="12" r="6.5" fill="none" stroke="#fff" stroke-width="1.5"/>
      <line x1="116.5" y1="12" x2="129.5" y2="12" stroke="#fff" stroke-width="1.2"/>
      <ellipse cx="123" cy="12" rx="2.8" ry="6.5" fill="none" stroke="#fff" stroke-width="1.2"/>
    </svg>

    <ul class="contact">
      <li>+1 555 284 6190</li>
      <li>lv@FundCorvel.com</li>
      <li>www.FundCorvel.com</li>
    </ul>
  </section>

  <section class="card card--back" aria-label="Business card back">
    <div class="back-split"></div>
    <div class="back-name">ALDERVANE</div>
  </section>

</main>
</body>
</html>
```